Halvick Ledgers & Advisory Tri-Fold Brochure (8.5"x11")

I need a professional looking brochure for my bookkeeping business. I am looking for something professional yet casual (not too corporate looking). I have attached a sample brochure that will outline the areas and a copy of our logo. I'd like to stick with shades of blue. The final product should communicate professional and personal.

Target Market(s)

Small service businesses.

Industry/Entity Type

Business

Font styles to use
Sans Serif

Requirements
Must have
• Professional looking photos of people in areas where it asks for a picture.

```html
<!DOCTYPE html>
<html lang="en">
<head>
<meta charset="utf-8">
<title>Halvick Ledgers &amp; Advisory – Brochure Inside</title>
<link rel="stylesheet" href="https://fonts.googleapis.com/css2?family=Nunito:wght@700;800&family=Didact+Gothic&display=swap">
<style>
  :root {
    --blue: #1c77c3;
    --sky: #2a9fe6;
    --rule: #2b86cf;
    --ink: #4b4b4b;
    --paper: #ffffff;
    --globe: #dfe3e8;
  }
  * { margin: 0; padding: 0; box-sizing: border-box; }
  html, body { width: 1200px; height: 927px; overflow: hidden; background: var(--paper); }
  .sheet { position: relative; width: 1200px; height: 927px; overflow: hidden; background: var(--paper); font-family: "Didact Gothic", sans-serif; color: var(--ink); }
  .globe-mark {
    position: absolute; left: -28px; top: -40px; width: 150px; height: 150px; border-radius: 50%;
    background: radial-gradient(circle at 55% 55%, #f3f5f7 0%, var(--globe) 70%, #cfd5dc 100%);
    opacity: .8;
  }
  .panel { position: absolute; top: 0; height: 927px; }
  .panel--services { left: 36px; width: 324px; }
  .panel--accounts { left: 425px; width: 339px; }
  .panel--why { left: 823px; width: 337px; }
  .block { position: absolute; left: 0; width: 100%; }
  .heading {
    font-family: "Nunito", sans-serif; font-weight: 800; color: var(--blue);
    font-size: 23px; line-height: 32px; text-align: center; white-space: nowrap;
  }
  .heading--title { font-size: 33px; line-height: 40px; }
  .heading--tall { line-height: 33px; }
  .heading--why { font-size: 32px; line-height: 44px; }
  .heading--pulse { text-align: left; font-size: 22px; line-height: 32px; letter-spacing: -.2px; }
  .copy { font-size: 17.5px; line-height: 22.4px; }
  .line { display: block; white-space: nowrap; text-align: justify; text-align-last: justify; }
  .line--end { text-align-last: left; }
  .service-list { list-style: none; font-size: 17.5px; line-height: 22.4px; padding-left: 53px; }
  .benefits { list-style: none; text-align: center; font-family: "Nunito", sans-serif; font-weight: 700; color: var(--sky); font-size: 24px; line-height: 33.4px; }
  .gap { display: block; height: 22.4px; }
  .rule { position: absolute; height: 1.5px; background: var(--rule); }
</style>
</head>
<body>
<main class="sheet">
  <div class="globe-mark" role="img" aria-label="Faint wireframe globe decoration"></div>

  <section class="panel panel--services">
    <h1 class="block heading heading--title" style="top:119px">SERVICES</h1>
    <div class="rule" style="top:161px; left:42px; width:227px"></div>

    <h2 class="block heading" style="top:186px">Full Charge Bookkeeping</h2>
    <div class="block copy" style="top:241px">
      <span class="line">We can manage all aspects of your</span>
      <span class="line">bookkeeping and business financials</span>
      <span class="line">and communicate to you as much and as</span>
      <span class="line line--end">often as you want.</span>
    </div>
    <div class="rule" style="top:348px; left:51px; width:225px"></div>

    <h2 class="block heading heading--tall" style="top:360px">Cash Management (Bill Pay &amp;<br>Invoicing) &amp; Vendor<br>Management</h2>
    <div class="block copy" style="top:482px">
      <span class="line">We can handle every step from</span>
      <span class="line">receiving bills, communicating with</span>
      <span class="line">vendor and paying bills. We take a lot</span>
      <span class="line">pride in helping our clients save money</span>
      <span class="line">and one way is negotiating with vendors</span>
      <span class="line line--end">and finding appropriate discounts.</span>
    </div>
    <div class="rule" style="top:637px; left:42px; width:227px"></div>

    <h2 class="block heading" style="top:645px">Financial Statements</h2>
    <div class="block copy" style="top:700px">
      <span class="line">Profit and Loss – Balance Sheet –</span>
      <span class="line">Statement of Cash Flow – Industry</span>
      <span class="line line--end">Specific</span>
      <span class="line">We accurately prepare monthly,</span>
      <span class="line">quarterly &amp; annual financial statements</span>
      <span class="line">in a timely manner. We also take the</span>
      <span class="line">time to review these statements with</span>
      <span class="line">you so that you understand the financial</span>
      <span class="line line--end">health of your business.</span>
    </div>
  </section>

  <section class="panel panel--accounts">
    <h2 class="block heading" style="top:32px">Account Reconciliations</h2>
    <div class="block copy" style="top:86px">
      <span class="line">From bank account to credit card</span>
      <span class="line">statements to vendor statements. We</span>
      <span class="line">reconcile all of your accounts that impact</span>
      <span class="line line--end">your finances.</span>
    </div>
    <div class="rule" style="top:194px; left:62px; width:225px"></div>

    <h2 class="block heading" style="top:205px">Professional liaison</h2>
    <div class="block copy" style="top:261px">
      <span class="line">We will work directly with your other</span>
      <span class="line">business partners – Bankers, CPA,</span>
      <span class="line">Insurance, Payroll, Attorney… Need a</span>
      <span class="line">loan? We will work directly with your</span>
      <span class="line">banker to make the process as simple as</span>
      <span class="line">possible. Does your CPA need some</span>
      <span class="line">data? Let us take care of that while you</span>
      <span class="line line--end">continue making your customers happy.</span>
    </div>
    <div class="rule" style="top:460px; left:55px; width:225px"></div>

    <h2 class="block heading" style="top:469px">Business Services</h2>
    <ul class="block service-list" style="top:531px">
      <li>Budget</li>
      <li>Create Proper Financial Systems</li>
      <li>Projections</li>
      <li>Customized Reporting</li>
      <li>Protection Planning</li>
      <li>Benchmarking</li>
      <li>Online Filing Cabinet (Paperless)</li>
    </ul>
    <div class="rule" style="top:707px; left:55px; width:225px"></div>

    <h2 class="block heading" style="top:716px">Exit/Succession Planning</h2>
    <div class="block copy" style="top:772px">
      <span class="line">We help you prepare your business for the</span>
      <span class="line">next transition – planned (retirement) or</span>
      <span class="line">unplanned (health). You've sacrificed to</span>
      <span class="line">build this business (asset) we can help you</span>
      <span class="line">transition it in the most efficient and</span>
      <span class="line line--end">valuable way.</span>
    </div>
  </section>

  <section class="panel panel--why">
    <h2 class="block heading heading--why" style="top:48px">Why Outsource<br>Bookkeeping?</h2>
    <ul class="block benefits" style="top:159px">
      <li>Save Time</li>
      <li>Save Money</li>
      <li>Expertise</li>
      <li>Focused Staff</li>
      <li>Technology</li>
      <li>Experience</li>
    </ul>
    <div class="rule" style="top:365px; left:42px; width:225px"></div>

    <h2 class="block heading heading--pulse" style="top:420px">The Financial Numbers are the<br>Heart Beat of an organization</h2>
    <div class="block copy" style="top:510px">
      <span class="line line--end">The Process</span>
      <span class="gap"></span>
      <span class="line line--end">Contact Us – we like to hear from you</span>
      <span class="line line--end">No-Obligation Consultation</span>
      <span class="gap"></span>
      <span class="line">Review Current Process – identify</span>
      <span class="line line--end">strengths and weaknesses</span>
      <span class="gap"></span>
      <span class="line">Recommend and implement new</span>
      <span class="line line--end">bookkeeping process</span>
      <span class="gap"></span>
      <span class="line line--end">Ongoing bookkeeping partnership</span>
      <span class="gap"></span>
      <span class="line">Provide your company with more value</span>
      <span class="line">and service to keep earning your business</span>
      <span class="line line--end">(ongoing)</span>
    </div>
  </section>
</main>
</body>
</html>
```